New Business card design to reflect rebrand

I would like a business card design with a good base colour for our new logo and also a placeholder for a profile pic of the card holder. the design needs to be editable to the point that we can easily change the picture of the person and use that design for printmerlo etc. we are looking at a metalic finish business card so will need a good base colour to bring out the finish.

Target Market(s)

prospective customers

Industry/Entity Type

Business

Contact Information for Business Card

I would like one editable design that we can change the name of the card holder and profile picture. The design need to be in a format that be send to printmerlo etc.

Our address is Fenwick Lodge, Copse Lane, Lindley Oakmoor, GU14 3TP Tel no. 01483 556172

Requirements
Must have
• place holder for a profile pic for the card holder. in AI or preferably PSD format

```html
<!DOCTYPE html>
<html lang="en">
<head>
<meta charset="utf-8">
<title>Calvorne Workplace Services – Business Card</title>
<link rel="stylesheet" href="https://fonts.googleapis.com/css2?family=Source+Sans+3:wght@400;600;700&display=swap">
<style>
  :root {
    --stage: #000000;
    --card: #333437;
    --card-edge: #3a3b3e;
    --accent: #e8721c;
    --ink: #f2f2f2;
    --photo-dark: #1f2230;
    --photo-light: #8a8f9a;
  }
  * { margin: 0; padding: 0; box-sizing: border-box; }
  html, body {
    width: 1200px; height: 900px; overflow: hidden;
    background: var(--stage);
    font-family: "Source Sans 3", "Myriad Pro", Arial, sans-serif;
  }
  .stage { position: relative; width: 1200px; height: 900px; }
  .card {
    position: absolute; top: 271px;
    width: 457px; height: 281px;
    background: radial-gradient(ellipse at 60% 40%, var(--card-edge), var(--card));
    border-radius: 14px; overflow: hidden;
  }
  .card--front { left: 137px; }
  .card--back { left: 626px; }

  .profile-photo {
    position: absolute; left: 0; top: 0;
    width: 191px; height: 281px;
    background: linear-gradient(180deg, var(--photo-light) 0%, #5a5f6c 35%, var(--photo-dark) 70%);
  }
  .holder-name {
    position: absolute; left: 239px; top: 76px;
    color: var(--accent); font-weight: 700; font-size: 16px;
  }
  .contact-list { position: absolute; left: 239px; top: 121px; list-style: none; }
  .contact-list li {
    display: flex; align-items: center; gap: 6px;
    color: var(--ink); font-size: 13px; line-height: 20px;
  }
  .contact-list svg { width: 9px; height: 9px; fill: var(--accent); }
  .address {
    position: absolute; left: 240px; top: 179px;
    color: var(--ink); font-size: 13px; line-height: 18px; font-style: normal;
  }
  .brand-name {
    position: absolute; left: 0; right: 0; top: 118px;
    text-align: center; color: var(--accent);
    font-weight: 600; font-size: 30px; letter-spacing: 3px; line-height: 34px;
    text-transform: uppercase;
  }
  .brand-name span { display: block; font-size: 17px; letter-spacing: 4px; line-height: 24px; }
</style>
</head>
<body>
<main class="stage">
  <section class="card card--front">
    <div class="profile-photo" role="img" aria-label="Profile photo of the card holder in a dark suit"></div>
    <h1 class="holder-name">Martin Ashby</h1>
    <ul class="contact-list">
      <li>
        <svg viewBox="0 0 10 10" aria-hidden="true"><path d="M2 0.5l2 2-1 1.2c.6 1.3 1.6 2.3 2.9 2.9l1.2-1 2 2-1.3 1.7C4.5 9.2.8 5.5.3 1.8z"/></svg>
        01483 556172
      </li>
      <li>
        <svg viewBox="0 0 10 10" aria-hidden="true"><path d="M0 2h10v.6L5 5.6 0 2.6z M0 3.8l5 3 5-3V8H0z"/></svg>
        info@calvorne.com
      </li>
    </ul>
    <address class="address">Fenwick Lodge, Copse Lane,<br>Lindley Oakmoor, GU14 3TP</address>
  </section>

  <section class="card card--back">
    <p class="brand-name">Calvorne<span>Workplace Services</span></p>
  </section>
</main>
</body>
</html>
```